Animal Horse & Bedding Company Needs a Website Coded & Designed

We need a website for a new animal bedding and feed company that is visually grabbing and vibrant. We would like to see a website that displays trust, quality and confidence. Needs to be responsive and mobile friendly for all browsers and coded for both Android & IOS. SEO is also important.

Joomla or Wordpress – must be both desktop and mobile friendly with fast page load speed. Need the ability to edit ourselves in Wordpress or Joomla.

Full details attached below with some layout and content ideas.

Coding

Coded - Design and coding required

Number of Pages Required

5+ page

Font styles to use
Sans Serif

Requirements
Must have
• Needs to be responsive and mobile friendly for all browsers and coded for both Android & IOS. SEO is also important.

Wordpress – must be both desktop and mobile friendly with fast page load speed. Need the ability to edit ourselves in Wordpress.

Logo Colours:
Dark Brown
CMYK: 50 / 70 / 80 / 70
Pantone: 4625C

Orange
CMYK: 0 / 50 / 100 / 0
Pantone: 144C
Nice to have
• Use picture of building attached and super impose logo on building.

```html
<!DOCTYPE html>
<html lang="en">
<head>
<meta charset="utf-8">
<title>Harvest Bale — Bedding &amp; Feed</title>
<link href="https://fonts.googleapis.com/css2?family=Montserrat:wght@400;500;600;700&display=swap" rel="stylesheet">
<style>
:root{
  --orange:#f7941d;
  --orange-deep:#f08a12;
  --orange-soft:#fbb040;
  --brown:#3f2417;
  --brown-mid:#4a2c1e;
  --barn-red:#a8302a;
  --field-green:#5d7a46;
  --ink:#3a3a3a;
  --text:#555;
  --white:#fff;
}
*{box-sizing:border-box;margin:0;padding:0}
html,body{width:1200px;height:4016px;overflow:hidden}
body{position:relative;font-family:'Montserrat',sans-serif;color:var(--ink);background:var(--white)}
.abs{position:absolute}
a{color:inherit;text-decoration:none}

/* header */
.site-header{position:absolute;left:0;top:0;width:1200px;height:268px;background:linear-gradient(#fff,#f3f0ec)}
.brand{left:97px;top:20px;display:flex;align-items:center;gap:12px}
.brand-dot{width:40px;height:40px;border-radius:50%;background:var(--orange)}
.brand-name{font-weight:700;font-size:26px;color:var(--brown);letter-spacing:1px}
.nav{left:430px;top:40px;font-size:12px;font-weight:500;color:var(--brown)}
.nav a{position:absolute;white-space:nowrap}
.nav .active{color:var(--orange)}
.btn-quote{left:950px;top:27px;width:153px;height:38px;border-radius:19px;background:var(--orange);color:#fff;font-size:11px;font-weight:700;display:flex;align-items:center;justify-content:center}
.hero-title{left:0;width:1200px;top:138px;text-align:center;font-size:38px;font-weight:600;color:var(--brown);letter-spacing:1px}
.hero-sub{left:0;width:1200px;top:186px;text-align:center;font-size:25px;font-weight:500;color:var(--orange);letter-spacing:12px}
.btn-learn{left:539px;top:234px;width:134px;height:40px;border-radius:20px;background:var(--orange);color:#fff;font-size:11px;font-weight:700;display:flex;align-items:center;justify-content:center}
.hero-photo{left:0;top:268px;width:1200px;height:427px;
  background:
    radial-gradient(ellipse 22% 30% at 18% 78%,rgba(168,48,42,.95),rgba(168,48,42,0)),
    radial-gradient(ellipse 26% 34% at 50% 72%,rgba(178,52,44,.95),rgba(178,52,44,0)),
    radial-gradient(ellipse 22% 36% at 86% 72%,rgba(160,44,40,.95),rgba(160,44,40,0)),
    radial-gradient(ellipse 40% 16% at 55% 58%,rgba(215,215,212,.8),rgba(215,215,212,0)),
    linear-gradient(#9fb0b8 0%,#7d9180 9%,#3f5a35 16%,#6e8a55 30%,#86985f 44%,#9a8f74 60%,#8d5a4a 75%,#6f6358 100%)}
.hero-arrow{top:325px;width:30px;height:36px}

/* about */
.about-mark{left:156px;top:720px;width:342px;height:456px;display:flex;flex-direction:column;align-items:center;justify-content:center;gap:26px}
.about-mark .circle{width:220px;height:220px;border-radius:50%;background:var(--orange)}
.about-mark .name{font-size:32px;font-weight:700;color:var(--brown);letter-spacing:1px}
.section-heading{font-size:34px;font-weight:600;color:var(--brown)}
.section-heading .accent{color:var(--orange)}
.about-heading{left:584px;top:800px}
.rule{height:3px;width:59px;background:var(--orange)}
.about-rule{left:584px;top:849px}
.about-copy{left:586px;top:878px;width:505px;font-size:12.5px;line-height:21px;color:var(--text)}
.about-copy p{margin-bottom:21px}

/* feature tiles */
.tile{top:1254px;height:293px;color:#fff;text-align:center;display:flex;flex-direction:column;align-items:center;padding-top:62px}
.tile-quality{left:0;width:397px;background:radial-gradient(ellipse at 35% 40%,#fba83a,var(--orange) 60%,#f38b14)}
.tile-service{left:397px;width:404px;background:radial-gradient(ellipse at 50% 40%,#5a4232,#3f2d22 70%,#33241b)}
.tile-cost{left:801px;width:399px;background:radial-gradient(ellipse at 60% 40%,#fbab3f,var(--orange-deep) 65%,#ee8610)}
.tile svg{width:58px;height:66px}
.tile h3{font-size:21px;font-weight:500;line-height:23px;margin-top:14px}
.tile p{font-size:11px;line-height:19px;margin-top:10px;width:270px}

/* bedding */
.bedding{left:0;top:1547px;width:1200px;height:879px;background:linear-gradient(#fdfcfa,#f5ebde 55%,#fdfbf8)}
.bedding-heading{left:0;width:1200px;top:1628px;text-align:center}
.bedding-rule{left:570px;top:1675px}
.orbit{left:391px;top:1708px;width:414px;height:414px;border-radius:50%;border:1.5px solid #b9a89a}
.horse-photo{left:414px;top:1731px;width:368px;height:368px;border-radius:50%;
  background:
    radial-gradient(ellipse 30% 40% at 50% 45%,rgba(150,72,34,.95),rgba(150,72,34,0)),
    linear-gradient(#dfe6e8 0%,#c9cfca 22%,#8a7e6a 34%,#b89a6a 60%,#d1b887 80%,#a98a5c 100%)}
.node{width:10px;height:10px;border-radius:50%;background:var(--orange)}
.benefit{width:74px;height:74px;border-radius:50%;display:flex;align-items:center;justify-content:center}
.benefit.o{background:var(--orange)}
.benefit.d{background:var(--brown-mid)}
.benefit svg{width:38px;height:38px}
.benefit-label{font-size:14px;line-height:19px;color:var(--brown)}
.benefit-label.r{text-align:right}
.btn-bedding{left:508px;top:2321px;width:188px;height:49px;border-radius:25px;background:var(--brown);color:#fff;font-size:13px;font-weight:700;display:flex;align-items:center;justify-content:center}

/* feed */
.feed{left:0;top:2426px;width:1200px;height:654px;background:linear-gradient(135deg,#f7921a,#f9a334 50%,#f6901a)}
.feed-heading{left:0;width:1200px;top:2490px;text-align:center;color:#fff}
.feed-intro{left:187px;width:826px;top:2545px;text-align:center;font-size:12.5px;line-height:21px;color:#fff}
.feed-item{display:flex;align-items:center;gap:10px;color:#fff;font-size:13px;font-weight:700;line-height:16px}
.feed-item svg{width:42px;height:42px;flex:none}
.feed-photo{left:745px;top:2622px;width:397px;height:393px;
  background:
    radial-gradient(ellipse 30% 24% at 58% 30%,rgba(196,172,98,1),rgba(196,172,98,0) 100%),
    radial-gradient(ellipse 24% 20% at 42% 72%,rgba(110,70,42,1),rgba(110,70,42,0) 100%),
    radial-gradient(ellipse 48% 48% at 50% 50%,#3a332c 70%,rgba(58,51,44,0) 72%)}
.btn-feed{left:519px;top:2976px;width:160px;height:46px;border-radius:23px;border:2px solid #fff;color:#fff;font-size:13px;font-weight:700;display:flex;align-items:center;justify-content:center}

/* delivery */
.map{left:137px;top:3150px;width:447px;height:379px;
  background:
    radial-gradient(ellipse 70% 30% at 45% 18%,#6b2a17 60%,rgba(107,42,23,0) 100%),
    radial-gradient(ellipse 55% 42% at 48% 62%,#f2a11e 70%,rgba(242,161,30,0) 100%)}
.delivery-heading{left:662px;top:3200px;color:var(--orange);line-height:40px}
.delivery-rule{left:664px;top:3281px}
.delivery-copy{left:668px;top:3312px;width:430px;font-size:12.5px;line-height:22px;color:var(--text)}
.btn-contact{left:665px;top:3424px;width:144px;height:43px;border-radius:22px;border:2px solid var(--brown);color:var(--orange);font-size:12px;font-weight:700;display:flex;align-items:center;justify-content:center}

/* footer */
.site-footer{left:0;top:3607px;width:1200px;height:409px;background:var(--brown)}
.foot-brand{left:104px;top:3690px;width:260px;display:flex;flex-direction:column;align-items:center;gap:12px}
.foot-brand .brand-dot{width:44px;height:44px}
.foot-brand .brand-name{color:#fff;font-size:28px}
.socials{left:168px;top:3814px;display:flex;gap:10px}
.socials span{width:30px;height:30px;border-radius:50%;background:var(--orange)}
.foot-title{font-size:14px;font-weight:500;color:#fff;letter-spacing:.5px}
.foot-list{font-size:11px;color:#fff;line-height:26px;list-style:none}
.contact-row{display:flex;align-items:center;gap:12px;font-size:10px;color:#fff}
.contact-row svg{width:14px;height:14px;flex:none}
.email-field{left:865px;top:3724px;width:230px;height:34px;border:1px solid #8a7364;border-radius:17px;color:#cbbcb0;font-size:10px;padding-left:20px;display:flex;align-items:center}
.btn-subscribe{left:869px;top:3773px;width:133px;height:32px;border-radius:16px;background:var(--orange);color:#fff;font-size:10px;font-weight:700;display:flex;align-items:center;justify-content:center}
.copyright{left:0;width:1200px;top:3963px;text-align:center;font-size:10px;color:#cbbcb0}
</style>
</head>
<body>

<header class="site-header">
  <div class="abs brand"><span class="brand-dot"></span><span class="brand-name">HARVEST BALE</span></div>
  <nav class="abs nav">
    <a class="active" style="left:14px">HOME</a>
    <a style="left:103px">ABOUT</a>
    <a style="left:198px">FEED</a>
    <a style="left:279px">BEDDING</a>
    <a style="left:386px">CONTACT US</a>
  </nav>
  <a class="abs btn-quote">REQUEST QUOTE ›</a>
  <h1 class="abs hero-title">WELCOME TO HARVEST BALE</h1>
  <div class="abs hero-sub">BEDDING &amp; FEED</div>
  <a class="abs btn-learn">LEARN MORE ›</a>
</header>
<div class="abs hero-photo" role="img" aria-label="Aerial view of the red barns and paddocks of the farm"></div>
<svg class="abs hero-arrow" style="left:36px" viewBox="0 0 30 36"><path d="M20 4 8 18l12 14" fill="none" stroke="#fff" stroke-width="3"/></svg>
<svg class="abs hero-arrow" style="left:1156px" viewBox="0 0 30 36"><path d="M10 4l12 14-12 14" fill="none" stroke="#fff" stroke-width="3"/></svg>

<section>
  <div class="abs about-mark"><span class="circle"></span><span class="name">HARVEST BALE</span></div>
  <h2 class="abs section-heading about-heading"><span class="accent">ABOUT</span> HARVEST BALE</h2>
  <div class="abs rule about-rule"></div>
  <div class="abs about-copy">
    <p>Looking for the best bedding and feed for your horse, livestock or household pet look no further. We use premium locally sourced straw and hay in all of our products and are committed in providing quality products and service.</p>
    <p>Your animal deserves the very best in health and comfort to keep them healthy, strong and happy. Our products are designed for horses, livestock (goats, cattle and sheep), small caged animals (rabbits, guinea pigs and more).</p>
    <p>Harvest Bale offers supply and delivery of fresh bedding as well as removal of waste bedding. Let us deliver you a container of fresh straw and haul your waste bedding away. A full service solution that is sustainable and responsible.</p>
  </div>
</section>

<section>
  <div class="abs tile tile-quality">
    <svg viewBox="0 0 58 66" fill="none" stroke="#fff" stroke-width="2"><circle cx="29" cy="24" r="16"/><circle cx="29" cy="24" r="10"/><path d="M29 17l2 5h5l-4 3 2 5-5-3-5 3 2-5-4-3h5z"/><path d="M18 36l-6 18 8-3 4 7 5-15M40 36l6 18-8-3-4 7-5-15"/></svg>
    <h3>QUALITY<br>GUARANTEED</h3>
    <p>Grown for quality - 100% natural with no chemicals or additives</p>
  </div>
  <div class="abs tile tile-service">
    <svg viewBox="0 0 58 66" fill="none" stroke="#fff" stroke-width="2"><path d="M12 20a20 20 0 1 0 34 0"/><path d="M18 14l20 22M40 14L20 36"/></svg>
    <h3>FULL SERVICE<br>SOLUTION</h3>
    <p>Dedicated in providing a full service solution of bedding supply &amp; waste removal</p>
  </div>
  <div class="abs tile tile-cost">
    <svg viewBox="0 0 58 66" fill="none" stroke="#fff" stroke-width="2"><ellipse cx="29" cy="36" rx="20" ry="15"/><circle cx="36" cy="12" r="6"/><path d="M18 49v7M38 49v7M49 33h4"/></svg>
    <h3>CONVENIENT &amp; COST<br>EFFECTIVE</h3>
    <p>Compressed bags , pellets or bulk products saving in shipping costs</p>
  </div>
</section>

<section>
  <div class="abs bedding"></div>
  <h2 class="abs section-heading bedding-heading">BEDDING</h2>
  <div class="abs rule bedding-rule"></div>
  <div class="abs orbit"></div>
  <div class="abs horse-photo" role="img" aria-label="Chestnut horse lying in straw bedding"></div>

  <span class="abs node" style="left:451px;top:1763px"></span>
  <span class="abs node" style="left:719px;top:1752px"></span>
  <span class="abs node" style="left:386px;top:1929px"></span>
  <span class="abs node" style="left:799px;top:1929px"></span>
  <span class="abs node" style="left:446px;top:2060px"></span>
  <span class="abs node" style="left:737px;top:2060px"></span>
  <span class="abs node" style="left:592px;top:2119px"></span>

  <div class="abs benefit o" style="left:356px;top:1727px"><svg viewBox="0 0 38 38" fill="none" stroke="#fff" stroke-width="2"><path d="M19 4c9 8 9 22 0 28-9-6-9-20 0-28zM19 10v30"/></svg></div>
  <div class="abs benefit-label r" style="left:180px;width:160px;top:1742px">100% Natural<br>Chopped Straw</div>

  <div class="abs benefit d" style="left:303px;top:1898px"><svg viewBox="0 0 38 38" fill="none" stroke="#fff" stroke-width="2"><circle cx="19" cy="19" r="14"/><path d="M9 9l20 20"/></svg></div>
  <div class="abs benefit-label r" style="left:180px;width:106px;top:1925px">Low Dust</div>

  <div class="abs benefit o" style="left:365px;top:2066px"><svg viewBox="0 0 38 38" fill="none" stroke="#fff" stroke-width="2"><circle cx="19" cy="19" r="15"/><path d="M15 9h8M16 9v8l-6 11h18l-6-11V9"/></svg></div>
  <div class="abs benefit-label r" style="left:180px;width:172px;top:2082px">Chemical &amp;<br>Additive Free</div>

  <div class="abs benefit d" style="left:561px;top:2147px"><svg viewBox="0 0 38 38" fill="none" stroke="#fff" stroke-width="2"><circle cx="13" cy="13" r="5"/><circle cx="24" cy="22" r="7"/><circle cx="11" cy="26" r="4"/></svg></div>
  <div class="abs benefit-label" style="left:498px;width:200px;top:2229px;text-align:center">Clean &amp; Highly<br>Absorbent</div>

  <div class="abs benefit o" style="left:761px;top:1723px"><svg viewBox="0 0 38 38" fill="none" stroke="#fff" stroke-width="2"><path d="M19 6l6 10H13zM8 30l6-10 6 10zM24 30l6-10 6 10z"/></svg></div>
  <div class="abs benefit-label" style="left:851px;width:220px;top:1742px">Environmentally Friendly –<br>Recyclable &amp; Compostable</div>

  <div class="abs benefit d" style="left:817px;top:1896px"><svg viewBox="0 0 38 38" fill="none" stroke="#fff" stroke-width="2"><circle cx="19" cy="19" r="14"/><path d="M5 19h28M19 5c-6 8-6 20 0 28M19 5c6 8 6 20 0 28"/></svg></div>
  <div class="abs benefit-label" style="left:905px;width:200px;top:1917px">Economic – less used<br>and less wasted</div>

  <div class="abs benefit o" style="left:753px;top:2066px"><svg viewBox="0 0 38 38" fill="none" stroke="#fff" stroke-width="2"><path d="M6 26h26v-6H12l-6 6zM14 20l4-8 6 2-2 6"/></svg></div>
  <div class="abs benefit-label" style="left:838px;width:200px;top:2084px">Cheaper than<br>Wood Shavings</div>

  <a class="abs btn-bedding">VIEW BEDDING ›</a>
</section>

<section>
  <div class="abs feed"></div>
  <h2 class="abs section-heading feed-heading">OUR FEED</h2>
  <p class="abs feed-intro">Hay cubes and pellets are made from premium hay offering a variety of animals a feed that is non-GMO and packed with natural nutrients. These pellets and cubes are less bulky to handle, store and ship. As well, they reduce the amount of wasted feed.</p>

  <div class="abs feed-item" style="left:118px;top:2652px"><svg viewBox="0 0 42 42" fill="none" stroke="#fff" stroke-width="2"><path d="M21 4c10 9 10 24 0 32-10-8-10-23 0-32zM21 10v30"/></svg>100% Natural</div>
  <div class="abs feed-item" style="left:354px;top:2652px"><svg viewBox="0 0 42 42" fill="none" stroke="#fff" stroke-width="2"><circle cx="21" cy="21" r="17"/><path d="M17 10h8M18 10v9l-7 12h20l-7-12v-9"/></svg>Chemical &amp;<br>Additive Free</div>
  <div class="abs feed-item" style="left:556px;top:2652px"><svg viewBox="0 0 42 42" fill="none" stroke="#fff" stroke-width="2"><path d="M8 16l10-6 10 6-10 6zM8 16v10l10 6V22M28 16v10l-10 6M22 26l8-5 8 5-8 5zM22 26v8l8 5 8-5v-8"/></svg>Available in<br>Pellets or Cubes</div>

  <div class="abs feed-item" style="left:116px;top:2750px"><svg viewBox="0 0 42 42" fill="none" stroke="#fff" stroke-width="2"><circle cx="12" cy="14" r="5"/><circle cx="26" cy="22" r="8"/><circle cx="10" cy="30" r="4"/><circle cx="36" cy="9" r="2"/></svg>Clean - Eliminates<br>Dust From Feeding<br>Baled Hay</div>
  <div class="abs feed-item" style="left:354px;top:2752px"><svg viewBox="0 0 42 42" fill="none" stroke="#fff" stroke-width="2"><path d="M9 10h24M12 10l3 28h12l3-28M17 15v18M21 15v18M25 15v18M17 10V6h8v4"/></svg>Eliminate Waste<br>In Feeding</div>
  <div class="abs feed-item" style="left:564px;top:2752px"><svg viewBox="0 0 42 42" fill="none" stroke="#fff" stroke-width="2"><path d="M4 22c6-10 10-10 14 0s8 10 14 0 6-6 8-4M4 30c6-10 10-10 14 0s8 10 14 0"/></svg>High Protein<br>Content</div>

  <div class="abs feed-item" style="left:112px;top:2846px"><svg viewBox="0 0 42 42" fill="none" stroke="#fff" stroke-width="2"><circle cx="17" cy="19" r="14"/><path d="M21 13h-6a3 3 0 0 0 0 6h4a3 3 0 0 1 0 6h-6M17 10v18"/><circle cx="34" cy="32" r="5"/></svg>Cost Effective</div>
  <div class="abs feed-item" style="left:350px;top:2848px"><svg viewBox="0 0 42 42" fill="none" stroke="#fff" stroke-width="2"><path d="M34 12a17 17 0 1 0 3 8"/><path d="M12 20l8 8 18-20"/></svg>Convenient</div>
  <div class="abs feed-item" style="left:564px;top:2846px"><svg viewBox="0 0 42 42" fill="none" stroke="#fff" stroke-width="2"><path d="M21 5l7 12H14zM8 36l7-12 7 12zM22 36l7-12 7 12z"/></svg>Less wasted<br>feed</div>

  <div class="abs feed-photo" role="img" aria-label="Two scoops holding hay pellets and mixed feed"></div>
  <a class="abs btn-feed">VIEW FEED ›</a>
</section>

<section>
  <div class="abs map" role="img" aria-label="Map of Canada in brown and the USA in orange showing delivery areas"></div>
  <h2 class="abs section-heading delivery-heading"><span class="accent">DELIVERY IN</span><br><span style="color:var(--brown)">CANADA &amp; USA</span></h2>
  <div class="abs rule delivery-rule"></div>
  <div class="abs delivery-copy">
    <p>Looking for the best bedding and feed for your horse, livestock or household pet look no further.</p>
    <p>We use premium locally sourced straw and hay in all of our products and are committed in providing quality products and service.</p>
  </div>
  <a class="abs btn-contact">CONTACT US</a>
</section>

<footer class="abs site-footer"></footer>
<div class="abs foot-brand"><span class="brand-dot"></span><span class="brand-name">HARVEST BALE</span></div>
<div class="abs socials"><span></span><span></span><span></span><span></span></div>

<h4 class="abs foot-title" style="left:427px;top:3688px">SITEMAP</h4>
<ul class="abs foot-list" style="left:427px;top:3717px">
  <li>Home</li><li>About Us</li><li>Our Bedding</li><li>Feed</li><li>Contact Us</li>
</ul>

<h4 class="abs foot-title" style="left:601px;top:3688px">CONTACT US</h4>
<div class="abs contact-row" style="left:601px;top:3724px"><svg viewBox="0 0 14 14"><path d="M7 1a4 4 0 0 1 4 4c0 3-4 8-4 8S3 8 3 5a4 4 0 0 1 4-4z" fill="#f7941d"/><circle cx="7" cy="5" r="1.5" fill="#3f2417"/></svg>48 Meadow Lane, Fieldtown</div>
<div class="abs contact-row" style="left:627px;top:3751px">00000, United States</div>
<div class="abs contact-row" style="left:601px;top:3776px"><svg viewBox="0 0 14 14"><path d="M3 1l3 3-2 2c1 2 2 3 4 4l2-2 3 3-2 3C6 13 1 8 1 3z" fill="#f7941d"/></svg>(555) 014-2290</div>
<div class="abs contact-row" style="left:601px;top:3813px"><svg viewBox="0 0 14 14"><rect x="1" y="3" width="12" height="8" fill="#f7941d"/><path d="M1 3l6 5 6-5" fill="none" stroke="#3f2417"/></svg>hello@harvestbale.example</div>

<h4 class="abs foot-title" style="left:865px;top:3686px">NEWSLETTER SIGN UP</h4>
<div class="abs email-field">Email address</div>
<a class="abs btn-subscribe">SUBSCRIBE</a>

<div class="abs copyright">© Copyright 2020 . Harvest Bale . All Right Reserved</div>

</body>
</html>
```